Packaging design for a reclosable bag for our product

We have a logo, and we need to put it on packaging for our product and while we want the look to be simple, we want it to follow good design principles and also contain spaces for other product descriptions.

There will be 5 sizes at launch so I'd like 5 variations, one for each size.

I've included a few mockups of the type of bag that I made but they are all just rough ideas that I had.

I want the brand to look scientific and methodical and even a bit quirky, as in "wow this is a serious product but also a bit unusual."

```html
<!DOCTYPE html>
<html lang="en">
<head>
<meta charset="utf-8">
<title>QV7 Bias Lighting – XL Pouch Front</title>
<link rel="stylesheet" href="https://fonts.googleapis.com/css2?family=Mulish:wght@400;500;800;900&display=swap">
<style>
  :root {
    --bg: #ffffff;
    --pouch: #161616;
    --pouch-strip: #222222;
    --strip-dark: #0c0c0c;
    --accent: #1a7fd0;
    --ink-on-accent: #101010;
    --text: #f2f2f2;
    --text-soft: #d9d9d9;
  }
  * { box-sizing: border-box; margin: 0; padding: 0; }
  html, body {
    width: 1200px; height: 1200px; overflow: hidden;
    background: var(--bg);
    font-family: "Mulish", sans-serif;
  }
  .canvas { position: relative; width: 1200px; height: 1200px; }

  .pouch {
    position: absolute; left: 290px; top: 150px;
    width: 620px; height: 900px;
    background: var(--pouch);
    border-radius: 22px 22px 4px 4px;
    overflow: hidden;
  }
  .side-strip {
    position: absolute; left: 0; top: 0; bottom: 0; width: 96px;
    background: var(--pouch-strip);
  }
  .side-strip .divider {
    position: absolute; left: 0; right: 0; top: 628px; height: 28px;
    background: var(--strip-dark);
  }
  .size-band {
    position: absolute; left: 0; right: 0; top: 656px; bottom: 0;
    background: var(--accent);
  }
  .size-label {
    position: absolute; left: 50%; bottom: 38px;
    transform: translateX(-50%) rotate(-90deg);
    transform-origin: center;
    white-space: nowrap;
    color: var(--ink-on-accent);
    font-size: 36px; line-height: 1;
    width: 0; display: flex; justify-content: center;
  }
  .size-label span { display: inline-block; }
  .size-label .size-num { font-weight: 900; font-size: 42px; margin-right: 8px; }
  .size-label .size-unit { font-weight: 500; }
  .size-label-wrap {
    position: absolute; left: 0; right: 0; bottom: 40px; height: 180px;
    display: flex; align-items: center; justify-content: center;
  }
  .size-label-wrap .size-label {
    position: static; transform: rotate(-90deg); width: auto;
  }

  .front-copy {
    position: absolute; left: 121px; top: 468px;
    color: var(--text);
  }
  .brand-name {
    font-weight: 800; font-size: 78px; line-height: 1;
    letter-spacing: -3px; color: #ffffff;
  }
  .product-name {
    margin-top: 26px;
    font-weight: 400; font-size: 41px; line-height: 1;
  }
  .product-size-text {
    margin-top: 10px;
    font-weight: 400; font-size: 23px; line-height: 1; color: var(--text-soft);
  }
  .size-code {
    margin-top: 22px;
    font-weight: 900; font-size: 42px; line-height: 1;
    color: var(--accent);
  }
  .spec-line {
    font-weight: 400; font-size: 26px; line-height: 1.3; color: var(--text-soft);
  }
  .spec-line.first { margin-top: 20px; }
</style>
</head>
<body>
<main class="canvas">
  <section class="pouch" aria-label="QV7 Bias Lighting XL pouch front">
    <div class="side-strip">
      <div class="divider"></div>
      <div class="size-band">
        <div class="size-label-wrap">
          <div class="size-label"><span class="size-num">5</span><span class="size-unit">meters</span></div>
        </div>
      </div>
    </div>

    <div class="front-copy">
      <div class="brand-name">QV7</div>
      <h1 class="product-name">Bias Lighting</h1>
      <p class="product-size-text">Extra large</p>
      <p class="size-code">XL</p>
      <p class="spec-line first">Simulated D65 CRI 90+</p>
      <p class="spec-line">6500K White Bias Lighting</p>
    </div>
  </section>
</main>
</body>
</html>
```